Flat bootstrap design for existing site

I'm looking for a modern flat design based around an existing logo. This has to be a custom design (no external templates), and implemented into a bootstrap framework.

The logo is attached as 2 versions - choose whichever you want, that flows better with whatever design you choose.

Added screenshots of the existing site (currently using the default bootstrap layouts). Please make your designs around those pages in the screenshots (i.e. the homepage only has the postal code input and the header). The active page has 3 screenshots, because I wanted to illustrate the other states that would be visible (in the table rows).

This is a moving/junk removal website, just for some context.

Here's some example websites (flat designs) that I like, just to give you an idea of what I'm after.

https://www.plimvora.com/
https://dacklow.com/
https://trevanu.com/
https://quobrintal.com/en/

Coding

Coded - Design and coding required

Number of Pages Required

5+ page

Colors

Designer to choose colors to be used in the design.

Requirements
Must have
• It must be a modern/simple flat design, that is built around the existing logo (attached).
• It has to be implemented using bootstrap.

```html
<!DOCTYPE html>
<html lang="en">
<head>
<meta charset="utf-8">
<title>Trundlo – Alternate Time</title>
<link href="https://fonts.googleapis.com/css2?family=Montserrat:wght@500;600;700;800&family=Roboto:wght@300;400;500&display=swap" rel="stylesheet">
<style>
:root{
  --sky:#38bdf0;
  --sky-deep:#1a8fd0;
  --white:#ffffff;
  --violet:#5b4fc0;
  --violet-text:#5a50b0;
  --ink:#4a4a55;
  --muted:#a3a3ad;
  --selected:#38bdf0;
  --green:#8dc63f;
  --footer-ink:#4a4a70;
  --social:#8b84c4;
}
*{margin:0;padding:0;box-sizing:border-box}
html,body{width:1200px;height:752px;overflow:hidden}
body{position:relative;background:var(--sky);font-family:"Roboto",sans-serif;color:var(--ink)}
.brand{position:absolute;left:144px;top:18px;font-family:"Montserrat",sans-serif;font-weight:800;font-size:32px;color:var(--white);letter-spacing:1px}
.nav{position:absolute;top:22px;left:559px;display:flex;align-items:center;font-family:"Montserrat",sans-serif;font-weight:600;font-size:11px;color:var(--white);letter-spacing:.4px}
.nav a{color:inherit;text-decoration:none}
.nav .link{margin-right:26px;line-height:35px}
.nav .driver{background:var(--sky-deep);padding:0 12px;line-height:35px;margin-right:16px}
.user{display:flex;align-items:center;color:var(--violet);font-weight:500;font-size:12px;letter-spacing:0}
.user .avatar{width:17px;height:17px;border-radius:50%;background:var(--violet);margin-right:6px}
.user svg{margin-left:4px}
.card{position:absolute;left:144px;top:102px;width:912px;height:488px;background:var(--white);box-shadow:0 4px 18px rgba(0,60,110,.12)}
.card h1{position:absolute;left:23px;top:36px;font-weight:400;font-size:19px;color:var(--violet-text)}
.calendar{position:absolute;left:16px;top:112px;width:290px}
.cal-head{position:relative;height:30px;text-align:center;font-size:16px;color:var(--violet-text);line-height:30px}
.cal-head svg{position:absolute;top:8px}
.cal-grid{display:grid;grid-template-columns:repeat(7,41.3px);grid-auto-rows:31.8px;text-align:center;font-size:16px;font-weight:300;align-items:center;justify-items:center}
.cal-grid .dow{font-weight:500;color:var(--ink);height:34px;line-height:34px}
.cal-grid .out{color:var(--muted)}
.cal-grid .day{width:32px;height:27px;line-height:27px}
.cal-grid .selected{background:var(--selected);color:var(--white)}
.time{position:absolute;left:350px;top:210px;width:160px;height:110px;font-size:16px;font-weight:500;color:var(--ink)}
.time svg{position:absolute}
.time .val{position:absolute;top:44px}
.time .pm{position:absolute;left:104px;top:38px;width:33px;height:27px;background:var(--green);color:var(--white);text-align:center;line-height:27px;font-size:16px}
.send{position:absolute;left:24px;top:412px;width:185px;height:36px;background:var(--violet);color:var(--white);font-family:"Montserrat",sans-serif;font-weight:600;font-size:11px;letter-spacing:.5px;text-align:center;line-height:36px}
.scene{position:absolute;left:1010px;top:520px;width:190px;height:167px;border-radius:120px 0 0 0;background:linear-gradient(160deg,#8fd6f6,#5fc4ef)}
.footer{position:absolute;left:0;top:687px;width:1200px;height:58px;background:var(--white)}
.footer p{position:absolute;left:144px;top:24px;font-size:12px;color:var(--footer-ink)}
.social{position:absolute;left:987px;top:22px;display:flex;gap:6px}
.social span{width:19px;height:19px;background:var(--social);border-radius:2px}
.band{position:absolute;left:0;top:745px;width:1200px;height:7px;background:var(--violet)}
</style>
</head>
<body>
<div class="brand">TRUNDLO</div>
<nav class="nav">
  <a class="link" href="#">BOOK</a>
  <a class="link" href="#">HOW IT WORKS</a>
  <a class="driver" href="#">BECOME A DRIVER</a>
  <span class="user"><span class="avatar"></span>hollis@mailbay.com
    <svg width="9" height="6" viewBox="0 0 9 6"><path d="M1 1l3.5 3.5L8 1" fill="none" stroke="currentColor" stroke-width="1.5"/></svg></span>
</nav>

<main class="card">
  <h1>Select an alternate date and time that you would like to send.</h1>
  <div class="calendar">
    <div class="cal-head">
      <svg style="left:8px" width="10" height="14" viewBox="0 0 10 14"><path d="M8 1L2 7l6 6" fill="none" stroke="#5b4fc0" stroke-width="2.4"/></svg>
      July 2017
      <svg style="right:4px" width="10" height="14" viewBox="0 0 10 14"><path d="M2 1l6 6-6 6" fill="none" stroke="#5b4fc0" stroke-width="2.4"/></svg>
    </div>
    <div class="cal-grid">
      <span class="dow">Su</span><span class="dow">Mo</span><span class="dow">Tu</span><span class="dow">We</span><span class="dow">Th</span><span class="dow">Fr</span><span class="dow">Sa</span>
      <span class="day out">25</span><span class="day out">26</span><span class="day out">27</span><span class="day out">28</span><span class="day out">29</span><span class="day out">30</span><span class="day">1</span>
      <span class="day">2</span><span class="day">3</span><span class="day">4</span><span class="day">5</span><span class="day">6</span><span class="day">7</span><span class="day">8</span>
      <span class="day">9</span><span class="day">10</span><span class="day">11</span><span class="day">12</span><span class="day selected">13</span><span class="day">14</span><span class="day">15</span>
      <span class="day">16</span><span class="day">17</span><span class="day">18</span><span class="day">19</span><span class="day">20</span><span class="day">21</span><span class="day">22</span>
      <span class="day">23</span><span class="day">24</span><span class="day">25</span><span class="day">26</span><span class="day">27</span><span class="day">28</span><span class="day">29</span>
      <span class="day">30</span><span class="day">31</span><span class="day out">1</span><span class="day out">2</span><span class="day out">3</span><span class="day out">4</span><span class="day out">5</span>
    </div>
  </div>
  <div class="time">
    <svg style="left:8px;top:4px" width="16" height="10" viewBox="0 0 16 10"><path d="M1 9l7-7 7 7" fill="none" stroke="#5b4fc0" stroke-width="2.4"/></svg>
    <svg style="left:64px;top:4px" width="16" height="10" viewBox="0 0 16 10"><path d="M1 9l7-7 7 7" fill="none" stroke="#5b4fc0" stroke-width="2.4"/></svg>
    <span class="val" style="left:7px">08</span>
    <span class="val" style="left:40px">:</span>
    <span class="val" style="left:62px">30</span>
    <span class="pm">PM</span>
    <svg style="left:8px;top:96px" width="16" height="10" viewBox="0 0 16 10"><path d="M1 1l7 7 7-7" fill="none" stroke="#5b4fc0" stroke-width="2.4"/></svg>
    <svg style="left:64px;top:96px" width="16" height="10" viewBox="0 0 16 10"><path d="M1 1l7 7 7-7" fill="none" stroke="#5b4fc0" stroke-width="2.4"/></svg>
  </div>
  <div class="send">SEND ALTERNATE TIME</div>
</main>

<div class="scene" role="img" aria-label="Illustration of a mover beside a bin, a house and a branded van"></div>

<footer class="footer">
  <p>© 2017 TRUNDLO. All rights reserved.</p>
  <div class="social"><span></span><span></span><span></span></div>
</footer>
<div class="band"></div>
</body>
</html>
```